The quiet harbor with an elephant incorporated in the background

Target Market(s)

Real estate

Industry/Entity Type

Real Estate

Contact Information for Business Card

On back on want my name & number
In front I want the business name, "the quiet harbor", below to say staging & design

Logo Text

The quiet harbor

Font styles to use
Serif

Colors
000000

Requirements
Must have
• I want an elephant behind the writing in gold transperant

```html
<!DOCTYPE html>
<html lang="en">
<head>
<meta charset="UTF-8">
<title>The Quiet Harbor – Business Card</title>
<link rel="stylesheet" href="https://fonts.googleapis.com/css2?family=Cinzel:wght@400;500&family=Open+Sans:wght@400;600&family=Quicksand:wght@300;400&display=swap">
<style>
  :root {
    --charcoal: #2a2627;
    --amber: #fdb600;
    --gold-text: #f6b400;
    --gold-veil: rgba(246, 180, 0, 0.14);
    --gold-veil-edge: rgba(246, 180, 0, 0);
    --sub-grey: #9a9697;
    --white: #ffffff;
    --rule: rgba(255, 255, 255, 0.45);
    --backdrop: #e9e7e4;
  }
  * { margin: 0; padding: 0; box-sizing: border-box; }
  html, body {
    width: 1200px;
    height: 900px;
    overflow: hidden;
    background: var(--backdrop);
  }
  .canvas { position: relative; width: 1200px; height: 900px; }

  .card {
    position: absolute;
    overflow: hidden;
    background: var(--amber);
    box-shadow: 0 6px 18px rgba(0, 0, 0, 0.18);
  }

  .brand-name {
    font-family: "Cinzel", serif;
    font-weight: 400;
    color: var(--gold-text);
    white-space: nowrap;
    position: relative;
    z-index: 1;
  }
  .brand-tagline {
    font-family: "Quicksand", sans-serif;
    font-weight: 300;
    color: var(--sub-grey);
    white-space: nowrap;
    position: relative;
    z-index: 1;
  }

  /* Transparent gold elephant artwork behind the name */
  .elephant-artwork {
    position: absolute;
    border-radius: 50%;
    background: radial-gradient(ellipse at center, var(--gold-veil) 0%, var(--gold-veil) 45%, var(--gold-veil-edge) 72%);
    z-index: 0;
  }

  /* Front: contact side */
  .card--front { left: 78px; top: 34px; width: 588px; height: 364px; }
  .front-header {
    position: absolute; left: 0; top: 0; width: 100%; height: 156px;
    background: var(--charcoal);
  }
  .front-header .elephant-artwork { left: 200px; top: 14px; width: 260px; height: 130px; }
  .front-header .brand-name {
    position: absolute; left: 30px; top: 54px;
    font-size: 40px; letter-spacing: 3.5px;
  }
  .front-header .brand-tagline { position: absolute; left: 164px; top: 100px; font-size: 22px; }

  .person { position: absolute; left: 30px; top: 173px; color: var(--white); font-family: "Open Sans", sans-serif; }
  .person__name { font-size: 20px; font-weight: 600; line-height: 1.2; }
  .person__role { font-size: 15px; font-weight: 400; margin-top: 1px; }

  .contact-list { position: absolute; left: 0; top: 254px; width: 248px; list-style: none; }
  .contact-list li {
    display: flex; align-items: center;
    height: 32px; padding-left: 32px;
    font-family: "Open Sans", sans-serif; font-size: 15px; color: var(--white);
    border-bottom: 1px solid var(--rule);
  }
  .contact-list li:last-child { border-bottom: none; }
  .contact-list svg { width: 13px; height: 13px; margin-right: 12px; fill: var(--white); }

  /* Back: brand side */
  .card--back { left: 388px; top: 505px; width: 567px; height: 352px; }
  .back-band {
    position: absolute; left: 0; top: 80px; width: 100%; height: 182px;
    background: var(--charcoal);
  }
  .back-band .elephant-artwork { left: 153px; top: 12px; width: 260px; height: 160px; }
  .brand-mark {
    position: absolute; left: 259px; top: 22px; width: 50px; height: 50px;
    background: var(--gold-text);
    z-index: 1;
  }
  .back-band .brand-name {
    position: absolute; left: 0; width: 100%; top: 107px;
    text-align: center; font-size: 34px; letter-spacing: 2.2px;
  }
  .back-band .brand-tagline {
    position: absolute; left: 0; width: 100%; top: 147px;
    text-align: center; font-size: 19px;
  }
</style>
</head>
<body>
<main class="canvas">

  <section class="card card--front">
    <header class="front-header">
      <div class="elephant-artwork" role="img" aria-label="Transparent gold elephant illustration behind the business name"></div>
      <div class="brand-name">The Quiet Harbor</div>
      <div class="brand-tagline">staging &amp; design</div>
    </header>
    <div class="person">
      <div class="person__name">Daniel Moore</div>
      <div class="person__role">Managing Director</div>
    </div>
    <ul class="contact-list">
      <li>
        <svg viewBox="0 0 24 24" aria-hidden="true"><path d="M6.6 10.8a15.1 15.1 0 0 0 6.6 6.6l2.2-2.2c.3-.3.7-.4 1-.2 1.1.4 2.3.6 3.6.6.6 0 1 .4 1 1V20c0 .6-.4 1-1 1A17 17 0 0 1 3 4c0-.6.4-1 1-1h3.5c.6 0 1 .4 1 1 0 1.3.2 2.5.6 3.6.1.3 0 .7-.2 1z"/></svg>
        044-987 654 321
      </li>
      <li>
        <svg viewBox="0 0 24 24" aria-hidden="true"><path d="M2 5h20v14H2z M4 7v.5l8 5 8-5V7l-8 5z" fill-rule="evenodd"/></svg>
        hello@quietharbor.com
      </li>
      <li>
        <svg viewBox="0 0 24 24" aria-hidden="true"><path d="M10.6 13.4a1 1 0 0 1 0-1.4l4-4a1 1 0 1 1 1.4 1.4l-4 4a1 1 0 0 1-1.4 0zM8 20a5 5 0 0 1-3.5-8.5l2.2-2.2 1.4 1.4-2.2 2.2a3 3 0 0 0 4.2 4.2l2.2-2.2 1.4 1.4-2.2 2.2A5 5 0 0 1 8 20zm9.3-5.3-1.4-1.4 2.2-2.2a3 3 0 0 0-4.2-4.2l-2.2 2.2-1.4-1.4 2.2-2.2a5 5 0 0 1 7 7z"/></svg>
        www.quietharbor.com
      </li>
    </ul>
  </section>

  <section class="card card--back">
    <div class="back-band">
      <div class="elephant-artwork" role="img" aria-label="Transparent gold elephant illustration behind the business name"></div>
      <div class="brand-mark" aria-hidden="true"></div>
      <div class="brand-name">The Quiet Harbor</div>
      <div class="brand-tagline">staging &amp; design</div>
    </div>
  </section>

</main>
</body>
</html>
```